2 sided postcard for New Internet Customers

We would like a design for a two sided postcard (with room for mailing label), dimensions 9 1/4 by 6 1/4 to be sent via US Mail.

The postcard needs to include our logo (attached) and the text
Fiber Optic Internet
555-318-2094
http://www.brightmesh.example
Speeds up to 1 Gig, with packages starting at $55

These will be sent to people who do not have our service.

Since this is going to be "junk mail" we probably only have 1 second or less to capture someone's attention to encourage them to read the entire postcard.

We are a "mom and pop" telecommunications company that provides internet, phone, and television services on the fiber optic network that we designed, built, and maintain.

We started as a dial up ISP in 1995, and have extraordinary technical support based in Freeport PA, our customers actually get the speeds they pay for, and our service is highly reliable.

We have a slogan (which you can choose to use or ignore) which is
"I Got Zoomed with Pellworth"

Existing customers can earn a $50 credit for every new customer they refer to us. Unlike most large cable and internet companies we have very happy customers... some who have stayed with us for decades.

I've attached our previous postcard, which I really dislike. It does have a blank spot for where the mailing label should go.

Target Market(s)

New Internet Customers in Western Pennsylvania

Industry/Entity Type

Internet

Font styles to use
Other font styles liked:
• Just match our logo.

Colors

Designer to choose colors to be used in the design.

Requirements
Must have
• The postcard needs to include our logo, and the text Fiber Optic Internet 555-318-2094 http://www.brightmesh.example Speeds up to 1 Gig, with packages starting at $55
Nice to have
• The colors and fonts should look good with our logo.
Should not have
• Should not have small print or lots of text. Both sides need to capture attention.

```html
<!DOCTYPE html>
<html lang="en">
<head>
<meta charset="utf-8">
<title>Pellworth Fiber Optic Internet Postcard</title>
<link rel="stylesheet" href="https://fonts.googleapis.com/css2?family=Montserrat:wght@300;500;600;700;800;900&family=Kaushan+Script&display=swap">
<style>
:root{
  --page:#d0d0d0;
  --blue:#1a72c4;
  --blue-bright:#3d8fe0;
  --ink:#0b0b16;
  --bubble:rgba(10,10,24,.86);
  --white:#ffffff;
  --text-dark:#111111;
}
*{box-sizing:border-box;margin:0;padding:0}
html,body{width:843px;height:1200px;overflow:hidden;background:var(--page);font-family:"Montserrat",sans-serif}
.card{position:absolute;left:89px;width:666px;overflow:hidden;background:var(--white)}
.card--front{top:101px;height:449px}
.card--back{top:649px;height:450px}
.photo{position:absolute;top:0;left:0;height:100%;
  background:
    radial-gradient(ellipse 40% 30% at 70% 12%,rgba(40,220,200,.55),transparent 70%),
    radial-gradient(ellipse 35% 30% at 92% 20%,rgba(240,200,60,.45),transparent 70%),
    radial-gradient(ellipse 45% 30% at 55% 45%,rgba(255,120,60,.45),transparent 70%),
    radial-gradient(ellipse 60% 30% at 45% 78%,rgba(255,40,140,.7),transparent 70%),
    radial-gradient(ellipse 60% 25% at 60% 98%,rgba(110,60,220,.7),transparent 70%),
    linear-gradient(160deg,#1b1030 0%,#2a0f3a 45%,#3a0a36 75%,#160b30 100%)}
.card--front .photo{width:100%}
.card--back .photo{width:353px}
.panel{position:absolute;top:0;background:linear-gradient(180deg,rgba(0,0,0,.82) 0%,rgba(10,20,50,.7) 45%,rgba(26,114,196,.85) 100%);color:var(--white);text-align:center}
.card--front .panel{left:27px;width:219px;height:422px;border-radius:0 0 110px 110px}
.card--back .panel{left:27px;width:154px;height:297px;border-radius:0 0 77px 77px;background:linear-gradient(180deg,rgba(0,0,0,.8),rgba(0,0,0,.85))}
.brand-dot{position:absolute;left:50%;transform:translateX(-50%);border-radius:50%;background:var(--blue)}
.brand-name{position:absolute;left:0;right:0;font-weight:300;color:var(--white);letter-spacing:-.5px}
.tag{position:absolute;left:50%;transform:translateX(-50%);background:var(--blue);color:var(--white);font-weight:800;white-space:nowrap;letter-spacing:.5px}
.headline{position:absolute;left:0;right:0;font-weight:900;line-height:1;letter-spacing:-1px;color:var(--white)}
.connector{position:absolute;background:var(--white)}
.node{position:absolute;border:2px solid var(--white);border-radius:50%;background:transparent}
.pill{position:absolute;background:var(--white);border-radius:20px;display:flex;align-items:center;color:var(--text-dark);font-weight:800;white-space:nowrap}
.icon{display:flex;align-items:center;justify-content:center;background:var(--blue);border-radius:50%;border:2px solid var(--white);flex:none}
.bubble{position:absolute;border-radius:50%;background:var(--bubble);border:4px solid var(--blue-bright);color:var(--white);text-align:center;display:flex;flex-direction:column;align-items:center;justify-content:center;font-weight:600}
.accent{color:var(--blue-bright)}
.speed-label{font-weight:600}
.speed-row{display:flex;align-items:center;gap:6px}
.upto{font-weight:700;line-height:.85;text-align:left}
.gig{color:var(--blue-bright);font-weight:500;line-height:1;letter-spacing:-1px}
.gig b{font-weight:800}
.rule{height:1px;background:rgba(255,255,255,.35)}
.price{color:var(--blue-bright);font-weight:900;line-height:1;letter-spacing:-1px}
.price sup{font-size:.5em;vertical-align:.6em}
.slogan{position:absolute;font-family:"Kaushan Script",cursive;color:var(--white);text-align:center;line-height:1.05;text-shadow:0 0 3px var(--blue-bright),0 0 8px var(--blue)}
.mail-area{position:absolute;left:353px;top:0;width:313px;height:100%;background:var(--white)}
.stamp{position:absolute;left:227px;top:28px;width:58px;height:58px;border:1px solid var(--blue)}
.address-line{position:absolute;left:73px;width:255px;height:1px;background:var(--blue)}
</style>
</head>
<body>

<section class="card card--front">
  <div class="photo" role="img" aria-label="Close-up photograph of glowing multicoloured fiber optic strands"></div>

  <div class="panel">
    <div class="brand-dot" style="top:40px;width:96px;height:96px"></div>
    <div class="brand-name" style="top:157px;font-size:29px">Pellworth, Inc.</div>
    <div class="tag" style="top:210px;font-size:14px;padding:0 4px;line-height:18px">HIGHLY RELIABLE</div>
    <div class="headline" style="top:236px;font-size:54px">Fiber</div>
    <div class="headline" style="top:290px;font-size:54px">Optic</div>
    <div class="headline" style="top:348px;font-size:34px">Internet</div>
  </div>

  <div class="connector" style="left:142px;top:404px;width:524px;height:2px"></div>
  <div class="node" style="left:137px;top:400px;width:11px;height:11px;background:var(--blue)"></div>

  <div class="pill" style="left:262px;top:386px;height:36px;padding:0 12px 0 4px;gap:6px;font-size:17px">
    <span class="icon" style="width:30px;height:30px"><svg width="15" height="15" viewBox="0 0 24 24"><path fill="#fff" d="M6.6 10.8a15.1 15.1 0 0 0 6.6 6.6l2.2-2.2c.3-.3.7-.4 1-.2 1.1.4 2.3.6 3.6.6.6 0 1 .4 1 1V20c0 .6-.4 1-1 1A17 17 0 0 1 3 4c0-.6.4-1 1-1h3.5c.6 0 1 .4 1 1 0 1.3.2 2.5.6 3.6.1.3 0 .7-.2 1z"/></svg></span>
    555-318-2094
  </div>
  <div class="pill" style="left:448px;top:386px;height:36px;padding:0 12px 0 4px;gap:6px;font-size:13.5px">
    <span class="icon" style="width:30px;height:30px"><svg width="16" height="16" viewBox="0 0 24 24" fill="none" stroke="#fff" stroke-width="1.8"><circle cx="12" cy="12" r="9"/><ellipse cx="12" cy="12" rx="4" ry="9"/><path d="M3 12h18M4.5 7.5h15M4.5 16.5h15"/></svg></span>
    brightmesh.example
  </div>

  <div class="bubble" style="left:402px;top:45px;width:100px;height:100px;font-size:11px;line-height:1.2">
    <span>Get</span><span>the <span class="accent">Actual</span></span><span class="accent">Speeds</span><span>You Pay</span><span>For</span>
  </div>
  <div class="bubble" style="left:450px;top:95px;width:178px;height:178px">
    <div class="speed-label" style="font-size:16px">Speeds</div>
    <div class="speed-row"><span class="upto" style="font-size:16px">up<br>to</span><span class="gig" style="font-size:36px"><b>1</b> Gig</span></div>
    <div class="rule" style="width:150px;margin:6px 0 4px"></div>
    <div style="font-size:12.5px;font-weight:700">Packages starting at</div>
    <div class="price" style="font-size:46px"><sup>$</sup>55</div>
  </div>
  <div class="bubble" style="left:358px;top:210px;width:130px;height:130px;font-size:10.5px;line-height:1.25">
    <span>EXISTING<br>CUSTOMER?</span>
    <span class="rule" style="width:90px;margin:5px 0"></span>
    <span>Earn a <span class="accent" style="font-weight:800"><sup style="font-size:8px">$</sup>50</span></span>
    <span><span class="accent">credit</span> for every</span><span>new customer</span><span>you refer</span><span>to us</span>
  </div>
</section>

<section class="card card--back">
  <div class="photo" role="img" aria-label="Close-up photograph of glowing multicoloured fiber optic strands"></div>
  <div class="connector" style="left:257px;top:0;width:5px;height:100%;background:var(--blue)"></div>

  <div class="panel">
    <div class="brand-dot" style="top:18px;width:84px;height:84px"></div>
    <div class="brand-name" style="top:111px;font-size:20px">Pellworth, Inc.</div>
    <div class="tag" style="top:148px;font-size:10.5px;padding:0 3px;line-height:14px">HIGHLY RELIABLE</div>
    <div class="headline" style="top:166px;font-size:37px">Fiber</div>
    <div class="headline" style="top:203px;font-size:37px">Optic</div>
    <div class="headline" style="top:244px;font-size:24px">Internet</div>
  </div>

  <div class="connector" style="left:104px;top:286px;width:2px;height:164px"></div>
  <div class="node" style="left:100px;top:277px;width:10px;height:10px;background:var(--ink)"></div>

  <span class="icon" style="position:absolute;left:91px;top:311px;width:28px;height:28px"><svg width="14" height="14" viewBox="0 0 24 24"><path fill="#fff" d="M6.6 10.8a15.1 15.1 0 0 0 6.6 6.6l2.2-2.2c.3-.3.7-.4 1-.2 1.1.4 2.3.6 3.6.6.6 0 1 .4 1 1V20c0 .6-.4 1-1 1A17 17 0 0 1 3 4c0-.6.4-1 1-1h3.5c.6 0 1 .4 1 1 0 1.3.2 2.5.6 3.6.1.3 0 .7-.2 1z"/></svg></span>
  <div class="pill" style="left:31px;top:337px;width:147px;height:28px;justify-content:center;font-size:15px">555-318-2094</div>
  <span class="icon" style="position:absolute;left:91px;top:371px;width:28px;height:28px"><svg width="15" height="15" viewBox="0 0 24 24" fill="none" stroke="#fff" stroke-width="1.8"><circle cx="12" cy="12" r="9"/><ellipse cx="12" cy="12" rx="4" ry="9"/><path d="M3 12h18M4.5 7.5h15M4.5 16.5h15"/></svg></span>
  <div class="pill" style="left:25px;top:396px;width:160px;height:27px;justify-content:center;font-size:13px">brightmesh.example</div>

  <div class="slogan" style="left:186px;top:66px;width:148px;font-size:27px">I Got Zoomed<br>with<br>Pellworth</div>

  <div class="bubble" style="left:185px;top:223px;width:148px;height:148px;border-color:var(--blue-bright)">
    <div class="speed-label" style="font-size:13px">Speeds</div>
    <div class="speed-row"><span class="upto" style="font-size:13px">up<br>to</span><span class="gig" style="font-size:30px"><b>1</b> Gig</span></div>
    <div style="font-size:10.5px;font-weight:700;margin-top:6px">Packages starting at</div>
    <div class="price" style="font-size:38px"><sup>$</sup>55</div>
  </div>

  <div class="mail-area">
    <div class="stamp"></div>
    <div class="address-line" style="top:209px"></div>
    <div class="address-line" style="top:240px"></div>
    <div class="address-line" style="top:271px"></div>
    <div class="address-line" style="top:302px"></div>
  </div>
</section>

</body>
</html>
```